Design a Website for an IT Support Company

We are an IT support company that provides commercial IT support and services to small and medium sized businesses. We are in need of a website to be developed for our business.
We would like to work with someone who is either familiar with the IT field, or has developed a website for an IT support company in the past.
Some examples of designs/layouts that we like:
https://www.veldaworks.example/
http://www.marsbyquill.example/
http://817kq.example/
http://www.olbenstructures.example/
http://www.bykq.example/
I have attached a word document that gives a menu system/page layout format that we would like for our website as well as branch office phone numbers. Our logo is also attached that you can use for your design purposes. We currently do not have copy produced for all of the pages outlined in the word document, but would get this done during the project with the selected designer.
We would like the website to be SEO friendly & fully responsive. We would prefer a Wordpress format, however, we are open to HTML formats as well.

```html
<!DOCTYPE html>
<html lang="en">
<head>
<meta charset="utf-8">
<title>Vantora IT — Commercial IT Support and Services</title>
<link rel="stylesheet" href="https://fonts.googleapis.com/css2?family=Lato:wght@400;700&family=Mulish:wght@400;600;700&display=swap">
<style>
:root{
  --brand:#1a73bd;
  --brand-dark:#0f5f9f;
  --ink:#333;
  --muted:#8a8a8a;
  --nav:#555;
  --white:#fff;
  --data-bg:#5a5a5a;
  --cloud-bg:#1479c8;
  --voice-bg:#3d3a38;
  --contact-bg:#e6e6e6;
  --field-border:#d6d6d6;
}
*{box-sizing:border-box;margin:0;padding:0}
html,body{width:1200px;height:2782px;overflow:hidden;background:var(--white)}
body{position:relative;font-family:"Mulish",Arial,sans-serif;color:var(--ink)}
.abs{position:absolute}
ul{list-style:none}

/* header */
.site-header{position:absolute;left:0;top:0;width:1200px;height:106px;background:var(--white)}
.brand{position:absolute;left:120px;top:30px;display:flex;align-items:center;gap:12px}
.brand-dot{width:42px;height:42px;border-radius:50%;background:var(--brand)}
.brand-name{font-family:"Lato",Arial,sans-serif;font-weight:700;font-size:30px;color:#222}
.main-nav a{position:absolute;top:47px;font-family:"Lato",Arial,sans-serif;font-size:16px;color:var(--nav);text-decoration:none;letter-spacing:.3px}
.main-nav a.active{color:var(--brand)}

/* hero */
.hero{position:absolute;left:0;top:106px;width:1200px;height:580px;overflow:hidden}
.hero-photo{position:absolute;inset:0;background:linear-gradient(100deg,#3a4452 0%,#56606e 35%,#7c8694 60%,#5b6674 100%)}
.hero-kicker{position:absolute;top:200px;width:100%;text-align:center;font-family:"Lato",Arial,sans-serif;font-size:34px;color:var(--white)}
.hero-title{position:absolute;top:244px;width:100%;text-align:center;font-family:"Lato",Arial,sans-serif;font-weight:400;font-size:47px;color:var(--white)}
.hero-btn{position:absolute;left:519px;top:315px;width:158px;height:38px;border-radius:19px;background:var(--brand);color:var(--white);font-size:16px;display:flex;align-items:center;padding-left:24px}
.hero-btn .arrow{position:absolute;right:6px;top:6px;width:26px;height:26px;border-radius:50%;background:var(--white)}
.hero-chevron{position:absolute;left:580px;top:418px}
.slider-dots{position:absolute;left:529px;top:523px;display:flex;gap:10px}
.slider-dots span{width:26px;height:3px;background:var(--white)}

/* services intro */
.services-intro{position:absolute;top:686px;left:0;width:1200px;height:225px;text-align:center}
.services-mark{position:absolute;left:582px;top:30px;width:36px;height:36px;border-radius:50%;border:4px solid var(--brand)}
.section-title{font-family:"Mulish",Arial,sans-serif;font-weight:600;font-size:32px;color:#333}
.services-intro .section-title{position:absolute;top:92px;width:100%}
.services-intro p{position:absolute;top:138px;left:240px;width:720px;font-size:13.5px;line-height:24px;color:var(--muted)}

/* service bands */
.band{position:absolute;overflow:hidden;color:var(--white)}
.band-photo{position:absolute;inset:0}
.band h3{position:absolute;font-weight:400;font-size:28px}
.band ul{position:absolute;font-size:14px}
.band li{position:relative;padding-left:12px}
.band li::before{content:"";position:absolute;left:0;top:50%;margin-top:-4px;border-left:5px solid var(--white);border-top:4px solid transparent;border-bottom:4px solid transparent}
.band svg{position:absolute}

.band-data{left:0;top:911px;width:1200px;height:382px}
.band-data .band-photo{background:linear-gradient(90deg,#4e4e4e,#626262 50%,#555)}
.band-data h3{left:117px;top:90px}
.band-data ul li{height:33px;line-height:33px}
.band-data .col-a{left:119px;top:146px}
.band-data .col-b{left:371px;top:146px}

.band-cloud{left:0;top:1293px;width:601px;height:365px}
.band-cloud .band-photo{background:linear-gradient(120deg,#1a86d6,#1169b4)}
.band-voice{left:601px;top:1293px;width:599px;height:365px}
.band-voice .band-photo{background:linear-gradient(100deg,#2f2d2c,#4a4642 60%,#3a3734)}
.band-cloud h3,.band-voice h3{left:115px;top:76px}
.band-voice h3{left:61px}
.band-cloud ul,.band-voice ul{top:132px}
.band-cloud ul{left:116px}
.band-voice ul{left:63px}
.band-cloud li,.band-voice li{height:28px;line-height:28px}

/* why */
.why{position:absolute;left:0;top:1658px;width:1200px;height:522px}
.why-photo{position:absolute;left:141px;top:69px;width:394px;height:394px;border-radius:50%;background:radial-gradient(circle at 55% 40%,#c7c3bf,#8f8a86 60%,#5c5754)}
.why .section-title{position:absolute;left:556px;top:102px;font-weight:400}
.why p{position:absolute;left:562px;width:496px;font-size:13.5px;line-height:25px;color:var(--muted)}
.why .p1{top:162px}
.why .p2{top:264px}
.btn-solid{position:absolute;background:var(--brand);color:var(--white);font-size:14px;display:flex;align-items:center;justify-content:center}
.why .btn-solid{left:562px;top:371px;width:135px;height:38px}

/* contact */
.contact{position:absolute;left:0;top:2180px;width:1200px;height:506px;overflow:hidden}
.contact-photo{position:absolute;inset:0;background:linear-gradient(135deg,#d9d9d9,#efefef 45%,#e2e2e2 70%,#cfcfcf)}
.contact .section-title{position:absolute;top:66px;width:100%;text-align:center;font-weight:400;font-size:36px}
.field{position:absolute;left:132px;width:428px;height:40px;background:var(--white);border:1px solid var(--field-border);font-size:13px;color:var(--muted);padding:11px 16px}
.field.message{height:96px}
.contact .btn-solid{left:134px;top:383px;width:135px;height:37px;font-size:15px;letter-spacing:.5px}
.contact-divider{position:absolute;left:603px;top:139px;width:1px;height:296px;background:#bdbdbd}
.contact-info{position:absolute;left:683px;top:146px;font-size:13.5px;color:#444}
.contact-info li{position:relative;height:33px;line-height:33px}
.contact-info svg{position:absolute;left:-22px;top:9px}

/* footer */
.site-footer{position:absolute;left:0;top:2686px;width:1200px;height:96px;background:var(--white)}
.copyright{position:absolute;left:120px;top:35px;font-size:14px;color:#444}
.social{position:absolute;left:930px;top:33px;display:flex;gap:5px}
.social span{width:30px;height:30px;border-radius:50%;border:2px solid var(--brand)}
</style>
</head>
<body>

<header class="site-header">
  <div class="brand"><span class="brand-dot"></span><span class="brand-name">Vantora IT</span></div>
  <nav class="main-nav">
    <a class="active" href="#" style="left:584px">HOME</a>
    <a href="#" style="left:679px">SERVICES</a>
    <a href="#" style="left:799px">WHY VANTORA IT</a>
    <a href="#" style="left:981px">CONTACT</a>
  </nav>
</header>

<section class="hero">
  <div class="hero-photo" role="img" aria-label="Two technicians working at server racks in a data centre"></div>
  <p class="hero-kicker">IT Support company that Provides</p>
  <h1 class="hero-title">Commercial IT Support and Services</h1>
  <div class="hero-btn">Read More<span class="arrow"><svg width="26" height="26" viewBox="0 0 26 26"><path d="M11 8l5 5-5 5" fill="none" stroke="#1a73bd" stroke-width="2.5"/></svg></span></div>
  <svg class="hero-chevron" width="40" height="24" viewBox="0 0 40 24"><path d="M4 4l16 16L36 4" fill="none" stroke="#fff" stroke-width="4"/></svg>
  <div class="slider-dots"><span></span><span></span><span></span><span></span></div>
</section>

<section class="services-intro">
  <span class="services-mark"></span>
  <h2 class="section-title">Our Services</h2>
  <p>interdum vel blandit sed nulla In ullamcorper est eget tempor cursus neque mi consectetuer mi a ultricies massa est sed nisl Class aptent taciti sociosqu ad litora torquent per conubia</p>
</section>

<section class="band band-data">
  <div class="band-photo" role="img" aria-label="Dimmed server room background"></div>
  <h3>Data</h3>
  <ul class="col-a">
    <li>Managed IT Services</li><li>IT Support &amp; Consulting</li><li>IT Helpdesk Services</li><li>Network Security</li><li>Data Backup &amp; Recovery</li>
  </ul>
  <ul class="col-b">
    <li>Servers &amp; Virtualization</li><li>Remote Monitoring Services</li><li>Wireless Networking</li><li>Email &amp; Spam Threat Management</li><li>Structured Cabling</li>
  </ul>
  <svg style="left:733px;top:91px" width="215" height="215" viewBox="0 0 215 215" fill="none" stroke="#fff" stroke-width="9">
    <ellipse cx="95" cy="40" rx="85" ry="28"/>
    <path d="M10 40v120c0 16 38 28 85 28"/>
    <path d="M180 40v50"/>
    <path d="M10 82c0 16 38 28 85 28"/>
    <path d="M10 122c0 16 38 28 85 28"/>
    <circle cx="160" cy="160" r="47" fill="#5a5a5a"/>
    <path d="M138 160l16 16 28-30" stroke-width="10"/>
  </svg>
</section>

<section class="band band-cloud">
  <div class="band-photo" role="img" aria-label="Blue-tinted laptop with network graphics"></div>
  <h3>Cloud</h3>
  <ul>
    <li>Suitehub 365 Migrations</li><li>Nimbara Cloud Management Services</li><li>Cloud Migration Services</li><li>Hosted Virtual Servers</li><li>Hosted Telephone Systems</li>
  </ul>
  <svg style="left:399px;top:98px" width="160" height="160" viewBox="0 0 160 160" fill="none" stroke="#fff" stroke-width="5" stroke-linejoin="round">
    <path d="M50 90h72a22 22 0 0 0 0-44a34 34 0 0 0-64-10a26 26 0 0 0-8 54z"/>
    <path d="M6 110h24l40 14h30a8 8 0 0 1 0 16H68"/>
    <path d="M100 128l40-22a10 10 0 0 1 12 16l-50 30H30"/>
  </svg>
</section>

<section class="band band-voice">
  <div class="band-photo" role="img" aria-label="Dim office scene with a man on a phone call"></div>
  <h3>Voice</h3>
  <ul>
    <li>Starline Consulting</li><li>Business Telephone Systems</li><li>Multiple Office Phone Systems</li><li>Tallbrook Telephone Systems</li><li>SIP Trunks</li>
  </ul>
  <svg style="left:323px;top:98px" width="160" height="160" viewBox="0 0 160 160" fill="none" stroke="#fff" stroke-width="6">
    <path d="M26 100V78a54 54 0 0 1 108 0v22"/>
    <rect x="16" y="92" width="24" height="48" rx="12"/>
    <rect x="120" y="92" width="24" height="48" rx="12"/>
  </svg>
</section>

<section class="why">
  <div class="why-photo" role="img" aria-label="Support agent wearing a headset at a call centre"></div>
  <h2 class="section-title">Why Vantora IT</h2>
  <p class="p1">Praesent sit amet est In dictum dolor eu dictum porttitor enim felis viverra mi eget luctus massa purus quis odio Etiam nulla massa pharetra facilisis volutpat in imperdiet sit amet sem Aliquam nec erat at purus cursus interdum Vestibulum ligula augue bibendum accumsan</p>
  <p class="p2">vestibulum ut commodo a mi Morbi ornare gravida elit Integer congue augue et malesuada iaculis ipsum dui aliquet felis at cursus magna nisl nec elit Donec iaculis diam a nisi accumsan</p>
  <div class="btn-solid">READ MORE</div>
</section>

<section class="contact">
  <div class="contact-photo" role="img" aria-label="Grey desk with keyboard, notebook and pen"></div>
  <h2 class="section-title">Contact Us</h2>
  <div class="field" style="top:139px">First Name</div>
  <div class="field" style="top:183px">Email address</div>
  <div class="field" style="top:230px">Phone</div>
  <div class="field message" style="top:276px">Message</div>
  <div class="btn-solid">SUBMIT</div>
  <div class="contact-divider"></div>
  <ul class="contact-info">
    <li><svg width="12" height="16" viewBox="0 0 12 16"><path d="M6 0a6 6 0 0 0-6 6c0 4 6 10 6 10s6-6 6-10a6 6 0 0 0-6-6z" fill="#1a73bd"/><circle cx="6" cy="6" r="2.2" fill="#fff"/></svg>48 Larkfield Row Suite 2 Texas 75001 TX</li>
    <li><svg width="15" height="12" viewBox="0 0 15 12"><rect x="1" y="1" width="13" height="10" fill="none" stroke="#1a73bd" stroke-width="1.5"/><path d="M1 1l6.5 6L14 1" fill="none" stroke="#1a73bd" stroke-width="1.5"/></svg>info@vantorait.example</li>
    <li><svg width="15" height="15" viewBox="0 0 15 15"><path d="M3 1l3 3-2 2c1 2 3 4 5 5l2-2 3 3-2 2C7 14 1 8 1 3z" fill="none" stroke="#1a73bd" stroke-width="1.4"/></svg>Main Number: 972-555-0140</li>
    <li>Houston: 832-555-0182</li>
    <li>San Antonio: 210-555-0127</li>
    <li>Austin: 512-555-0163</li>
    <li>Tulsa: 918-555-0119</li>
    <li>Oklahoma City: 405-555-0175</li>
  </ul>
</section>

<footer class="site-footer">
  <p class="copyright">© 2017 Company Name&nbsp; All right reserved&nbsp; Term of Use</p>
  <div class="social"><span></span><span></span><span></span><span></span></div>
</footer>

</body>
</html>
```